Corvane Capital Business Cards

These are professional business cards that are for my family office.
Put fake emails and phone numbers as of now until I finalize those components. This family office controls my families investments, assets, and future. The cards should be professional.
..
.
.
.
I just uploaded another variation of a logo I would like to see as a business card to I am inbeteen which logo to use

Target Market(s)

business

Industry/Entity Type

business

Contact Information for Business Card

Professional, wealth related, finance related.

Requirements
Must have
• Logo

```html
<!DOCTYPE html>
<html lang="en">
<head>
<meta charset="utf-8">
<title>Corvane Capital Business Cards</title>
<link rel="stylesheet" href="https://fonts.googleapis.com/css2?family=Playfair+Display:wght@400&family=Tinos:wght@400;700&display=swap">
<style>
  :root {
    --gold: #c7ae70;
    --ink: #0b0b0b;
    --paper: #ffffff;
    --backdrop: #ececec;
  }
  * { box-sizing: border-box; margin: 0; padding: 0; }
  html, body {
    width: 1200px;
    height: 716px;
    overflow: hidden;
    background: var(--backdrop);
  }
  .sheet {
    position: relative;
    width: 1200px;
    height: 716px;
  }
  .card {
    position: absolute;
    left: 369px;
    width: 461px;
    height: 264px;
  }
  .card-front {
    top: 94px;
    background: var(--gold);
  }
  .card-back {
    top: 385px;
    background: var(--paper);
    font-family: "Tinos", "Times New Roman", serif;
    color: var(--ink);
  }
  .front-wordmark {
    position: absolute;
    left: 0;
    right: 0;
    top: 112px;
    text-align: center;
    font-family: "Playfair Display", Georgia, serif;
    font-weight: 400;
    font-size: 32px;
    letter-spacing: 0.5px;
    color: var(--paper);
    line-height: 1;
  }
  .back-wordmark {
    position: absolute;
    left: 18px;
    top: 29px;
    font-family: "Playfair Display", Georgia, serif;
    font-weight: 400;
    font-size: 20px;
    letter-spacing: 0.3px;
    color: var(--ink);
    line-height: 1;
  }
  .holder {
    position: absolute;
    left: 17px;
    top: 112px;
  }
  .holder-name {
    font-weight: 700;
    font-size: 18px;
    line-height: 1;
  }
  .holder-name .surname { color: var(--gold); }
  .holder-role {
    margin-top: 5px;
    font-size: 13px;
    line-height: 1;
  }
  .divider {
    position: absolute;
    left: 17px;
    top: 157px;
    width: 16px;
    height: 4px;
    background: var(--gold);
  }
  .contact {
    position: absolute;
    left: 17px;
    top: 181px;
    list-style: none;
    font-size: 13px;
    line-height: 19px;
  }
  .contact li { display: flex; align-items: center; gap: 4px; }
  .contact svg { width: 13px; height: 10px; fill: var(--gold); flex: none; }
  .band {
    position: absolute;
    top: 222px;
    height: 28px;
  }
  .band-dark { left: 0; width: 349px; background: var(--ink); }
  .band-gold { left: 385px; right: 0; background: var(--gold); }
</style>
</head>
<body>
<main class="sheet">
  <section class="card card-front" aria-label="Card front">
    <p class="front-wordmark">CORVANE CAPITAL</p>
  </section>

  <section class="card card-back" aria-label="Card back">
    <p class="back-wordmark">CORVANE CAPITAL</p>
    <div class="holder">
      <p class="holder-name">Elias <span class="surname">Harrow</span></p>
      <p class="holder-role">Founder</p>
    </div>
    <span class="divider"></span>
    <ul class="contact">
      <li>
        <svg viewBox="0 0 13 10" aria-hidden="true"><path d="M0 3.5C0 1.5 3 0.5 6.5 0.5S13 1.5 13 3.5L10.5 4.2 9.8 2.8H3.2L2.5 4.2ZM3 4.5H10L11.5 9.5H1.5Z"/></svg>
        555-214-8830
      </li>
      <li>
        <svg viewBox="0 0 13 10" aria-hidden="true"><path d="M0 0.5H13V1.2L6.5 5.6 0 1.2ZM0 2.4L6.5 6.8 13 2.4V9.5H0Z"/></svg>
        office@corvanecapital.com
      </li>
    </ul>
    <span class="band band-dark"></span>
    <span class="band band-gold"></span>
  </section>
</main>
</body>
</html>
```